Wordpress Design Project (Brindlow)

We need a wordpress design for an established auction and real estate company based in New Jersey. The winning design will incorporate a professional color scheme and company logo in a clean layout.

Industry/Entity Type

Real Estate

Requirements
Must have
• - We will require winning designer to provide a layered PSD (Adobe photoshop) concept file, along with any non-standard font files used.

Logo attached. Will hopefully post better logo shortly. Please use site design colors of your choice as the logo is black & white. A site client mentions liking is http://www.qelmarbidding.example/. Homepage content will be an auction list as seen at http://www.gavelroundup.example/?page=5

Horizontal Navigation menu with these pages:
Home - Auction Calendar - Appraisals - Services - Company Profile - News & Events - Testimonials - Contact Us

A slideshow element on the home page using one of the placeholder images provided (or stock if higher resolution image is necessary).

Sidebar widgets to be included are: Email sign-up form - Featured Auctions - Testimonial widget - 'Our Videos' widget; Social media icons somewhere in layout (facebook, twitter, RSS, and Youtube)

Homepage content is text:
BRINDLOW MANAGEMENT COMPANY was founded 90 years ago in 1921 by Harold Brindlow, which makes us one of the oldest commercial and industrial auction and appraisal companies in America.

We have conducted thousands of auctions, assisting a wide range of companies both large and small achieve maximum value for their capital assets.
Nice to have
• - Site will have drop down menus, nice to have a sample look for them on one of the primary menu items.

```html
<!DOCTYPE html>
<html lang="en">
<head>
<meta charset="utf-8">
<title>Brindlow Auctioneers &amp; Appraisers</title>
<link href="https://fonts.googleapis.com/css2?family=Roboto:ital,wght@0,400;0,500;0,700;1,400&family=Roboto+Condensed:wght@400&display=swap" rel="stylesheet">
<style>
:root{
  --black:#000;
  --ink:#333;
  --text:#555;
  --muted:#777;
  --rule:#dcdcdc;
  --blue:#1a6fd6;
  --blue-dark:#0d57b8;
  --nav:#1c1c1c;
  --footer:#ececec;
  --white:#fff;
  --social:#4a4a4a;
}
*{box-sizing:border-box;margin:0;padding:0}
html,body{width:1029px;height:1200px;overflow:hidden;background:var(--white)}
body{position:relative;font-family:Roboto,Arial,sans-serif;color:var(--text)}
.abs{position:absolute}
.header-band{left:0;top:0;width:1029px;height:219px;background:var(--black)}
.brand{left:106px;top:15px;width:247px;height:75px;background:var(--white);border:2px solid #ccc;display:flex;align-items:center;justify-content:center;gap:10px}
.brand-mark{width:22px;height:22px;background:var(--black)}
.brand-name{font-weight:700;font-size:30px;color:var(--black);letter-spacing:1px}
.search{left:711px;top:37px;width:216px;height:30px;background:var(--white);border:1px solid #ccc;border-radius:2px}
.search svg{position:absolute;right:8px;top:7px}
.search::before{content:"";position:absolute;right:28px;top:5px;width:1px;height:20px;background:#ddd}
.nav{left:103px;top:106px;width:823px;height:40px;background:var(--nav);display:flex;align-items:center}
.nav a{color:var(--white);text-decoration:none;font-size:10.5px;font-weight:500;height:40px;line-height:40px;padding:0 17px;white-space:nowrap}
.nav a.active{background:linear-gradient(var(--blue),var(--blue-dark));padding:0 12px}
.slider{left:103px;top:146px;width:823px;height:291px;background:linear-gradient(180deg,#7fb1e6 0%,#a9c8e8 30%,#b23a40 55%,#8c1e26 80%,#5a5a5a 100%)}
.dots{left:478px;top:419px;display:flex;gap:6px}
.dots span{width:8px;height:8px;border-radius:50%;background:rgba(255,255,255,.75)}
h2{position:absolute;font-family:"Roboto Condensed",Arial,sans-serif;font-weight:400;font-size:16px;color:var(--ink);letter-spacing:.3px;white-space:nowrap}
.photo{position:absolute}
.copy{position:absolute;left:317px;width:326px;font-size:10.3px;line-height:16.3px;text-align:justify;color:var(--text)}
.copy p+p{margin-top:16px}
.hr{position:absolute;height:1px;background:var(--rule)}
.news{position:absolute;width:260px;height:80px}
.news .thumb{position:absolute;left:0;top:0;width:67px;height:64px}
.news .body{position:absolute;left:70px;top:-4px;width:185px;font-size:9.8px;line-height:14.6px;color:var(--text);text-align:justify}
.news .title{color:var(--blue);font-size:11.6px;display:block;text-align:left;white-space:nowrap}
.news .date{color:#222}
.panel{position:absolute;left:669px;width:257px;border:1px solid var(--rule)}
.fa-text{left:806px;top:667px;width:113px;font-size:10.3px;line-height:12.5px;color:var(--blue);text-align:justify;position:absolute}
.fa-date{left:806px;top:728px;font-size:10.3px;color:#222;position:absolute}
.fa-btn{position:absolute;top:773px;font-size:10.3px;font-weight:500;color:#444;display:flex;align-items:center;gap:7px}
.quote{position:absolute;left:677px;top:857px;width:241px;font-size:10.3px;line-height:16.4px;font-style:italic;color:var(--muted);text-align:justify}
.author{position:absolute;left:677px;top:946px;font-size:10.6px;color:#444}
.author b{color:var(--blue);font-weight:700}
.email{left:677px;top:1025px;width:243px;height:31px;border:1px solid #ccc;font-size:10.3px;font-style:italic;color:#666;padding:9px 5px;position:absolute}
.signup{left:849px;top:1060px;width:71px;height:31px;background:linear-gradient(var(--blue),var(--blue-dark));color:var(--white);font-size:14px;font-weight:500;text-align:center;line-height:31px;border-radius:2px;position:absolute}
.footer{left:0;top:1136px;width:1029px;height:64px;background:var(--footer)}
.footer-links{left:106px;top:1156px;font-size:9.4px;color:#555;line-height:15px;position:absolute;white-space:nowrap}
.social{left:787px;top:1157px;display:flex;gap:6px;position:absolute}
.social span{width:24px;height:24px;background:var(--social)}
</style>
</head>
<body>
<div class="abs header-band"></div>
<div class="abs brand"><span class="brand-mark"></span><span class="brand-name">BRINDLOW</span></div>
<div class="abs search"><svg width="12" height="12" viewBox="0 0 12 12"><circle cx="5" cy="5" r="3.5" fill="none" stroke="#bbb" stroke-width="1.5"/><line x1="7.5" y1="7.5" x2="11" y2="11" stroke="#bbb" stroke-width="1.8"/></svg></div>
<nav class="abs nav">
  <a class="active" href="#">HOME</a><a href="#">AUCTION CALENDAR</a><a href="#">APPRAISALS</a><a href="#">SERVICES</a><a href="#">COMPANY PROFILE</a><a href="#">NEWS &amp; EVENTS</a><a href="#">TESTIMONIALS</a><a href="#">CONTACT US</a>
</nav>
<div class="abs slider" role="img" aria-label="Row of red semi trucks parked under a blue sky"></div>
<div class="abs dots"><span></span><span></span><span></span><span></span><span></span><span></span></div>

<h2 style="left:103px;top:451px">WELCOME TO BRINDLOW!</h2>
<div class="photo" role="img" aria-label="Gym interior with exercise machines" style="left:103px;top:484px;width:204px;height:172px;background:linear-gradient(160deg,#cfd3d6,#6d6f72 55%,#2e2f31)"></div>
<div class="copy" style="top:481px">
  <p>BRINDLOW MANAGEMENT COMPANY was founded 90 years ago in 1921 by Harold Brindlow, which makes us one of the oldest commercial and industrial auction and appraisal companies in America.We have conducted thousands of auctions, assisting a wide range of companies both large and small achieve maximum value for their capital assets.</p>
  <p>BRINDLOW MANAGEMENT COMPANY was founded 90 years ago in 1921 by Harold Brindlow, which makes us one of the oldest commercial and industrial auction and appraisal companies in America.We have conducted thousands of auctions, assisting a wide range of companies both large and small achieve maximum value for their capital assets.</p>
</div>
<div class="hr" style="left:103px;top:674px;width:540px"></div>

<h2 style="left:103px;top:683px">OUR SERVICES</h2>
<div class="photo" role="img" aria-label="Glass office building with landscaped lawn" style="left:103px;top:716px;width:204px;height:172px;background:linear-gradient(170deg,#e9edf1,#8d9aa6 50%,#5e8a3e 85%,#6fae3c)"></div>
<div class="copy" style="top:713px">
  <p>BRINDLOW MANAGEMENT COMPANY was founded 90 years ago in 1921 by Harold Brindlow, which makes us one of the oldest commercial and industrial auction and appraisal companies in America.We have conducted thousands of auctions, assisting a wide range of companies both large and small achieve maximum value for their capital assets.</p>
  <p>BRINDLOW MANAGEMENT COMPANY was founded 90 years ago in 1921 by Harold Brindlow, which makes us one of the oldest commercial and industrial auction and appraisal companies in America.We have conducted thousands of auctions, assisting a wide range of companies both large and small achieve maximum value for their capital assets.</p>
</div>
<div class="hr" style="left:103px;top:905px;width:540px"></div>

<h2 style="left:103px;top:914px">LATEST NEWS</h2>
<div class="news" style="left:103px;top:948px">
  <div class="thumb" role="img" aria-label="Office building exterior" style="background:linear-gradient(170deg,#dfe5ea,#7f8c98 60%,#5b7d3f)"></div>
  <div class="body"><span class="title">Perspiciatis unde omnis iste natus</span><span class="date">10 August, 2013</span><br>sit voluptatem accusantium doloremque laudantium, totam rem aperiam, eaque ipsa quae ab illo inventore veritatis et</div>
</div>
<div class="news" style="left:386px;top:948px">
  <div class="thumb" role="img" aria-label="Box trucks in a parking lot" style="background:linear-gradient(170deg,#8fb8e0,#e6e9ec 50%,#7d7f82)"></div>
  <div class="body"><span class="title">Perspiciatis unde omnis iste natus</span><span class="date">10 August, 2013</span><br>sit voluptatem accusantium doloremque laudantium, totam rem aperiam, eaque ipsa quae ab illo inventore veritatis et</div>
</div>
<div class="news" style="left:103px;top:1040px">
  <div class="thumb" role="img" aria-label="Brick commercial building" style="background:linear-gradient(170deg,#c9d6e2,#9a7650 55%,#6b6b6b)"></div>
  <div class="body"><span class="title">Perspiciatis unde omnis iste natus</span><span class="date">10 August, 2013</span><br>sit voluptatem accusantium doloremque laudantium, totam rem aperiam, eaque ipsa quae ab illo inventore veritatis et</div>
</div>
<div class="news" style="left:386px;top:1040px">
  <div class="thumb" role="img" aria-label="Red roofed buildings beside a road" style="background:linear-gradient(170deg,#d5dfe8,#a4473c 50%,#666)"></div>
  <div class="body"><span class="title">Perspiciatis unde omnis iste natus</span><span class="date">10 August, 2013</span><br>sit voluptatem accusantium doloremque laudantium, totam rem aperiam, eaque ipsa quae ab illo inventore veritatis et</div>
</div>

<h2 style="left:669px;top:451px">OUR VIDEOS</h2>
<div class="hr" style="left:669px;top:478px;width:257px"></div>
<div class="photo" role="img" aria-label="Video still of printing machinery in a workshop" style="left:669px;top:490px;width:257px;height:120px;background:linear-gradient(170deg,#9aa39a,#d8dcd4 50%,#5c5f58)"></div>
<svg class="abs" style="left:776px;top:534px" width="48" height="32" viewBox="0 0 48 32"><rect width="48" height="32" rx="6" fill="rgba(120,120,120,.75)"/><path d="M19 9 L32 16 L19 23 Z" fill="#fff"/></svg>

<h2 style="left:670px;top:628px">FEATURED AUCTIONS</h2>
<div class="panel" style="top:659px;height:135px"></div>
<div class="photo" role="img" aria-label="Ranch home surrounded by trees" style="left:677px;top:667px;width:119px;height:77px;background:linear-gradient(170deg,#dfe6ea,#5f8a3a 40%,#8a3d2e 65%,#7aa640)"></div>
<div class="fa-text">Lot 1 1.257+/- Ac w/ Ranch Home, Lot 2- 1.374+/- Ac Perked &amp; Surveyed</div>
<div class="fa-date">12 August, 2013</div>
<div class="hr" style="left:669px;top:765px;width:257px"></div>
<div class="hr" style="left:793px;top:769px;width:1px;height:20px"></div>
<div class="fa-btn" style="left:703px"><svg width="12" height="12" viewBox="0 0 12 12"><circle cx="5" cy="5" r="3.5" fill="none" stroke="#444" stroke-width="1.4"/><line x1="7.5" y1="7.5" x2="11" y2="11" stroke="#444" stroke-width="1.8"/></svg>DETAILS</div>
<div class="fa-btn" style="left:821px"><svg width="16" height="13" viewBox="0 0 16 13"><rect x="1" y="3" width="14" height="9" rx="1" fill="none" stroke="#444" stroke-width="1.4"/><rect x="5" y="1" width="5" height="3" fill="#444"/><circle cx="8" cy="7.5" r="2.5" fill="none" stroke="#444" stroke-width="1.4"/></svg>PHOTOS</div>

<div class="panel" style="top:811px;height:163px"></div>
<h2 style="left:677px;top:820px">TESTIMONIAL</h2>
<div class="hr" style="left:669px;top:847px;width:257px"></div>
<p class="quote">Sed ut perspiciatis unde omnis iste natus error sit voluptatem accusantium doloremque laudantium, totam rem aperiam, eaque ipsa quae ab illo inventore veritatis et quasi architecto beatae vitae dicta sunt explicabo.</p>
<p class="author"><b>Renata,</b> Lorem ipaum</p>

<div class="panel" style="top:983px;height:120px"></div>
<h2 style="left:676px;top:990px">NEWSLETTER SIGNUP</h2>
<div class="hr" style="left:669px;top:1017px;width:257px"></div>
<div class="email">Enter your Email</div>
<div class="signup">SIGNUP</div>

<footer class="abs footer"></footer>
<div class="footer-links">Home - Auction Calendar - Appraisals - Services - Company Profile - News &amp; Events - Testimonials - Contact Us<br>© 2013 Brindlow Auctioneers &amp; Appraisers</div>
<div class="social">
  <span role="img" aria-label="Social link"></span><span role="img" aria-label="Social link"></span><span role="img" aria-label="News feed link"></span><span role="img" aria-label="Video channel link"></span><span role="img" aria-label="Social link"></span>
</div>
</body>
</html>
```